Business Card Design

Want something very unique. No business, just personal. The image I submitted is for inspiration only.

Target Market(s)

friends and new acquaintances

Industry/Entity Type

Business

Contact Information for Business Card

Dora Malcott
Mesa Alta, NM
505-718-2946
doramalcott@quellmail.net

```html
<!DOCTYPE html>
<html lang="en">
<head>
<meta charset="utf-8">
<title>Dora Malcott – Personal Card</title>
<link rel="stylesheet" href="https://fonts.googleapis.com/css2?family=Advent+Pro:wght@400&family=Philosopher:wght@400&display=swap">
<style>
  :root {
    --stage: #ece8e1;
    --card-yellow: #f0b21a;
    --ink: #231f1c;
    --cream: #ecebd9;
    --photo-earth: #9a7b57;
    --photo-leaf: #7f8a4c;
    --photo-sky: #d9d6c6;
  }
  * { box-sizing: border-box; margin: 0; padding: 0; }
  html, body {
    width: 1200px;
    height: 504px;
    overflow: hidden;
    background: var(--stage);
  }
  .stage {
    position: relative;
    width: 1200px;
    height: 504px;
    display: flex;
    gap: 32px;
    padding: 92px 32px;
  }
  .card {
    position: relative;
    width: 552px;
    height: 320px;
    overflow: hidden;
    box-shadow: 0 6px 18px rgba(0,0,0,0.18);
  }
  .card-front { background: var(--card-yellow); }
  .card-front .swoosh {
    position: absolute;
    inset: 0;
    width: 100%;
    height: 100%;
  }
  .name-badge {
    position: absolute;
    left: 52px;
    top: 70px;
    width: 184px;
    height: 184px;
    border-radius: 50%;
    border: 5px solid var(--ink);
    padding: 6px;
    background: var(--card-yellow);
  }
  .name-badge-inner {
    width: 100%;
    height: 100%;
    border-radius: 50%;
    background: var(--cream);
    display: flex;
    align-items: center;
    justify-content: center;
  }
  .holder-name {
    font-family: "Advent Pro", sans-serif;
    font-weight: 400;
    font-size: 40px;
    line-height: 1.02;
    color: var(--ink);
    text-align: center;
  }
  .contact {
    position: absolute;
    right: 40px;
    top: 72px;
    list-style: none;
    font-family: "Philosopher", sans-serif;
    font-size: 15px;
    color: var(--ink);
    text-align: right;
  }
  .contact li {
    display: flex;
    align-items: center;
    justify-content: flex-end;
    gap: 4px;
    margin-bottom: 12px;
  }
  .contact svg { width: 14px; height: 14px; fill: var(--ink); flex: none; }
  .follow {
    position: absolute;
    right: 40px;
    top: 194px;
    font-family: "Philosopher", sans-serif;
    color: var(--ink);
    text-align: right;
  }
  .follow-title { font-size: 15px; margin-bottom: 4px; }
  .follow-list {
    list-style: none;
    display: flex;
    gap: 8px;
    justify-content: flex-end;
    font-size: 12px;
  }
  .card-back .photo {
    width: 100%;
    height: 100%;
    background:
      linear-gradient(180deg, var(--photo-sky) 0%, rgba(217,214,198,0) 30%),
      linear-gradient(135deg, var(--photo-leaf) 0%, var(--photo-earth) 55%, #b79b72 100%);
  }
</style>
</head>
<body>
<main class="stage">
  <section class="card card-front" aria-label="Card front">
    <svg class="swoosh" viewBox="0 0 552 320" aria-hidden="true">
      <path d="M296 0 L312 0 C268 90 282 230 408 320 L384 320 C262 238 244 96 296 0 Z" fill="var(--ink)"/>
      <path d="M328 20 C300 110 312 220 398 300 C318 240 296 130 328 20 Z" fill="var(--ink)"/>
    </svg>

    <div class="name-badge">
      <div class="name-badge-inner">
        <h1 class="holder-name">Dora<br>Malcott</h1>
      </div>
    </div>

    <ul class="contact">
      <li>
        <svg viewBox="0 0 24 24" aria-hidden="true"><path d="M12 2a7 7 0 0 0-7 7c0 5 7 13 7 13s7-8 7-13a7 7 0 0 0-7-7zm0 9.5A2.5 2.5 0 1 1 12 6.5a2.5 2.5 0 0 1 0 5z"/></svg>
        <span>Mesa Alta, NM</span>
      </li>
      <li>
        <svg viewBox="0 0 24 24" aria-hidden="true"><path d="M6.6 10.8a15 15 0 0 0 6.6 6.6l2.2-2.2a1 1 0 0 1 1-.25 11.4 11.4 0 0 0 3.6.57 1 1 0 0 1 1 1V20a1 1 0 0 1-1 1A17 17 0 0 1 3 4a1 1 0 0 1 1-1h3.5a1 1 0 0 1 1 1c0 1.25.2 2.45.57 3.57a1 1 0 0 1-.25 1z"/></svg>
        <span>505-718-2946</span>
      </li>
      <li>
        <svg viewBox="0 0 24 24" aria-hidden="true"><path d="M3 6h18v12H3z M3 6l9 7 9-7" fill="none" stroke="var(--ink)" stroke-width="2"/></svg>
        <span>doramalcott@quellmail.net</span>
      </li>
    </ul>

    <div class="follow">
      <p class="follow-title">Follow Us On</p>
      <ul class="follow-list">
        <li>Friendloop</li>
        <li>Chirpwire</li>
        <li>Worknest</li>
      </ul>
    </div>
  </section>

  <section class="card card-back" aria-label="Card back">
    <div class="photo" role="img" aria-label="Photograph of two people crouching beside resting cheetahs in a sunny rocky enclosure"></div>
  </section>
</main>
</body>
</html>
```